Business Card Design Can you design a business card design? Looking for something unique and differe

Can you design a business card design? Looking for something unique and different. Can you design a business card design? Looking for something unique and different.Can you design a business card design? Looking for something unique and different.Can you design a business card design? Looking for something unique and different.Can you design a business card design? Looking for something unique and different.Can you design a business card design? Looking for something unique and different.

Industry/Entity Type

Business

Contact Information for Business Card

Can you design a business card design? Looking for something unique and different.

Font styles to use
Serif

```html
<!DOCTYPE html>
<html lang="en">
<head>
<meta charset="utf-8">
<title>Business Card – Remedia</title>
<link rel="stylesheet" href="https://fonts.googleapis.com/css2?family=Varela+Round&family=Open+Sans:ital,wght@0,400;1,400&display=swap">
<style>
  :root {
    --page-bg: #ece8e4;
    --card-top: #f4f2f1;
    --card-bottom: #dcd7d4;
    --plum: #735a86;
    --plum-band: #7c6190;
    --ink: #1c1c1e;
    --text-dark: #2a2a2c;
    --icon: #4a4a4e;
  }
  * { margin: 0; padding: 0; box-sizing: border-box; }
  html, body {
    width: 1200px; height: 970px; overflow: hidden;
    background: var(--page-bg);
  }
  .business-card {
    position: absolute;
    left: 173px; top: 270px;
    width: 855px; height: 475px;
    background: linear-gradient(160deg, var(--card-top), var(--card-bottom));
    border: 1px solid #cfcac6;
    overflow: hidden;
    font-family: "Open Sans", Arial, sans-serif;
    color: var(--text-dark);
  }
  .holder-name {
    position: absolute; left: 41px; top: 48px;
    font-family: "Varela Round", Arial, sans-serif;
    font-size: 27px; color: var(--plum);
  }
  .holder-title {
    position: absolute; left: 41px; top: 90px;
    font-size: 16px; font-style: italic;
  }
  .contact-list {
    position: absolute; left: 41px; top: 214px;
    list-style: none;
  }
  .contact-list li {
    display: flex; align-items: center;
    height: 29px; font-size: 19px;
  }
  .contact-list svg { width: 20px; height: 16px; margin-right: 20px; fill: var(--icon); }
  .office-address {
    position: absolute; left: 41px; top: 323px;
    font-size: 19px; line-height: 29px;
  }
  .brand {
    position: absolute; left: 495px; top: 185px;
    display: flex; align-items: center; gap: 14px;
  }
  .brand-mark { width: 26px; height: 26px; background: var(--plum); }
  .brand-name {
    font-family: "Varela Round", Arial, sans-serif;
    font-size: 46px; color: var(--plum);
  }
  .card-wave { position: absolute; left: 0; bottom: 0; width: 855px; height: 475px; }
</style>
</head>
<body>
  <div class="business-card">
    <svg class="card-wave" viewBox="0 0 855 475" aria-hidden="true">
      <path fill="var(--plum-band)" d="M0,420 Q300,452 720,462 L720,475 L0,475 Z"/>
      <path fill="var(--ink)" d="M0,462 Q480,458 855,418 L855,475 L0,475 Z"/>
    </svg>

    <h1 class="holder-name">Your Long Name</h1>
    <p class="holder-title">Managing Director</p>

    <ul class="contact-list">
      <li>
        <svg viewBox="0 0 20 16"><path d="M2 5 Q10 0 18 5 L16 7 L13 5 L7 5 L4 7 Z M5 8 H15 L17 15 H3 Z"/></svg>
        00.00.00.0000
      </li>
      <li>
        <svg viewBox="0 0 20 16"><path d="M1 2 H19 V14 H1 Z M2 3 L10 9 L18 3 Z" fill-rule="evenodd"/></svg>
        yourname@yourwebsite.com
      </li>
      <li>
        <svg viewBox="0 0 20 16"><circle cx="10" cy="8" r="7"/><path d="M3 8 H17 M10 1 V15" stroke="#f0eeec" stroke-width="1.2"/></svg>
        www.yourwebsite.com
      </li>
    </ul>

    <p class="office-address">Your Commercial or office address<br>in just two line with pincode</p>

    <div class="brand">
      <span class="brand-mark"></span>
      <span class="brand-name">Remedia</span>
    </div>
  </div>
</body>
</html>
```